Wordpress - For IT, Cloud/Hosting, Residential/Commercial Construction Services

We are a holding company for service companies. We want the current Wordpress site modified or a new wordpress site completed. We want this site to be the parent website, that then has pull down menus linking to our other website (currently http://brightwallfix.com, http://q7v.host and would like it to be easy and fluid as we acquire more companies as we have with TKLS, Inc., B&J Construction, Brightwall Fix etc. Model after sites like Pemrose.com, Tallowbine.com, QDV.com,.vanterelm.com

------

The parent is the main site q7v Corp. Below that are sub corps and DBAs. q7v Corp stands for Quick 7 Venture Corp. q7v Offers IT manages services, 24x7 support, Monitoring NOC, Remote Hands, Onsite support services. We have acquired TKLS, Inc, B & J Construction, BrightwallFix.com. We plan to acquire/spin up many companies that offer service, support and installation offerings and will all be known as an q7v Corp Company for branding purposes. We recently had our logo done, but then ran it through 3d glass as we like the look better than the original works. We have original files in vector, but not the 3D galss door render.

Target Market(s)

IT Server and Desktop Support. Construction. Mold Remediation. Mergers and Acquisitions.

Industry/Entity Type

It Company

Coding

Coded - Design and coding required

Font styles to use
Sans Serif

Colors
0792cd

Requirements
Must have
• Clean interface. Modern design. Mobile device and multi browser support. Must be for Wordpress. Job posting with resume submission module.Hook to our Web hosting portal (Tormund) API into VexaLine Reseller portal, customer portal to allow payments to their account etc.. Easy to edit. Easy to add to, Press Release Section, Investor Relations etc.
Should not have
• Slow loading. Played out design. Over use of stock images. Copied from a competitor or something point to such.

```html
<!DOCTYPE html>
<html lang="en">
<head>
<meta charset="utf-8">
<title>Q7V Corp</title>
<link href="https://fonts.googleapis.com/css2?family=Poppins:wght@300;400;500;600&family=Lato:wght@400;700&display=swap" rel="stylesheet">
<style>
:root{
  --brand:#0a6fc2;
  --brand-bright:#1a84d4;
  --ink:#222;
  --body:#555;
  --line:#d9d9d9;
  --white:#fff;
}
*{box-sizing:border-box;margin:0;padding:0}
html,body{width:1200px;height:3136px;overflow:hidden}
body{position:relative;background:var(--white);font-family:"Lato",sans-serif;color:var(--body)}
.abs{position:absolute}
a{color:inherit;text-decoration:none}

/* header */
.topline{left:0;top:0;width:1200px;height:4px;background:var(--brand)}
.site-header{left:0;top:4px;width:1200px;height:84px;background:var(--white)}
.brand-name{font-family:"Poppins",sans-serif;font-weight:600;color:var(--brand);white-space:nowrap;line-height:1}
.site-header .brand-name{left:112px;top:29px;font-size:24px}
.main-nav{left:387px;top:0;height:84px;display:flex;align-items:center;font-family:"Poppins",sans-serif;font-size:16px;color:#333}
.main-nav a{display:flex;align-items:center;height:84px;padding:0 16px}
.main-nav a.active{background:var(--brand);color:var(--white);padding:0 18px}
.main-nav .caret{margin-left:6px}
.dropdown{left:846px;top:66px;width:242px;background:var(--white);border:1px solid #ccc;font-family:"Poppins",sans-serif;font-size:14px;color:#333;z-index:5;box-shadow:0 2px 6px rgba(0,0,0,.12)}
.dropdown a{display:block;height:48px;line-height:48px;padding-left:34px;border-bottom:1px solid #ccc}
.dropdown a:last-child{border-bottom:0}

/* hero */
.hero{left:0;top:88px;width:1200px;height:514px;background:linear-gradient(100deg,#1c3550 0%,#2f5f8a 35%,#4a86b8 60%,#1f4a75 100%)}
.hero-title{left:0;top:270px;width:1200px;text-align:center;font-family:"Poppins",sans-serif;font-weight:600;font-size:112px;color:var(--white);letter-spacing:2px;line-height:1}
.scroll-down{left:573px;top:510px;width:54px;height:54px}

.section-title{left:0;width:1200px;text-align:center;font-family:"Poppins",sans-serif;font-weight:400;font-size:48px;color:var(--ink)}

.provide-card{top:767px;width:234px}
.provide-card .photo{width:234px;height:166px}
.provide-card h3{font-family:"Poppins",sans-serif;font-weight:500;font-size:18px;color:var(--ink);margin-top:16px;line-height:30px}
.provide-card p{font-size:14px;color:#444;line-height:24px}
.provide-card .more{display:block;margin-top:10px;font-size:14px;color:var(--brand)}

.wwd-back{left:94px;top:1172px;width:466px;height:310px;background:var(--brand)}
.wwd-photo{left:111px;top:1156px;width:468px;height:309px;background:linear-gradient(120deg,#c4c9b2 0%,#a9b06a 40%,#e2b35a 70%,#8f8f7a 100%)}
.wwd-title{left:619px;top:1146px;font-family:"Poppins",sans-serif;font-size:48px;font-weight:300;color:var(--ink)}
.wwd-text{left:620px;top:1222px;width:470px;font-size:15px;line-height:30px;color:#444}
.btn{background:var(--brand);color:var(--white);font-family:"Poppins",sans-serif;font-weight:500;text-align:center}
.wwd-btn{left:620px;top:1442px;width:138px;height:41px;line-height:41px;font-size:15px}

.blog-card{top:1659px;width:315px;height:415px;border:1px solid var(--line)}
.blog-card .photo{position:relative;width:313px;height:199px}
.blog-card .tag{position:absolute;left:0;bottom:0;padding:0 28px;height:28px;line-height:28px;background:var(--brand);color:var(--white);font-family:"Poppins",sans-serif;font-size:13px;font-weight:500}
.blog-card h3{margin:22px 22px 0;font-family:"Poppins",sans-serif;font-weight:500;font-size:18px;line-height:29px;color:var(--ink)}
.blog-card p{margin:20px 22px 0;font-size:14px;line-height:31px;color:#666}
.blog-card p a{color:var(--brand);text-decoration:underline}

.help-band{left:0;top:2167px;width:1200px;height:408px;background:radial-gradient(ellipse at 30% 40%,#2a4a66 0%,#142a40 55%,#0a1828 100%)}
.tile{width:161px;height:138px;background:rgba(16,115,190,.88);color:var(--white);text-align:center;font-size:15px}
.tile svg{display:block;margin:22px auto 10px}
.help-box{left:456px;top:2228px;width:631px;height:288px;background:var(--brand-bright)}
.help-box h2{position:absolute;left:52px;top:44px;font-family:"Poppins",sans-serif;font-weight:300;font-size:33px;color:var(--white)}
.help-box p{position:absolute;left:54px;top:104px;width:420px;font-size:14px;line-height:22px;color:#e8f3fb}
.help-box .field{position:absolute;left:54px;top:161px;width:541px;height:48px;background:var(--white);padding-left:20px;line-height:48px;font-size:13px;color:#888}
.help-box .send{position:absolute;left:54px;top:226px;font-family:"Poppins",sans-serif;font-size:15px;font-weight:500;color:var(--white);text-decoration:underline}

.footer-brand{left:0;top:2658px;width:1200px;text-align:center;font-size:34px}
.socials{left:471px;top:2739px;display:flex;gap:14px}
.socials span{width:40px;height:40px;border:2px solid var(--brand);border-radius:50%;display:block}
.foot-col{top:2806px}
.foot-col h4{font-family:"Poppins",sans-serif;font-weight:400;font-size:19px;color:#333;margin-bottom:22px}
.foot-col a{display:block;font-size:13px;line-height:29px;color:#444}
.foot-input{height:39px;border:1px solid #bbb;font-size:12px;color:#888;padding:0 16px;line-height:37px}
.foot-send{left:669px;top:3010px;width:77px;height:28px;line-height:28px;font-size:14px}
.copyright{left:0;top:3092px;width:1200px;text-align:center;font-size:12px;color:#444}
</style>
</head>
<body>

<div class="abs topline"></div>
<header class="abs site-header">
  <div class="abs brand-name">Q7V Corp</div>
  <nav class="abs main-nav">
    <a class="active" href="#">Home</a>
    <a href="#">About Us</a>
    <a href="#">Solutions</a>
    <a href="#">Support</a>
    <a href="#">Partners</a>
    <a href="#">Blog</a>
    <a href="#">Companies<svg class="caret" width="10" height="7" viewBox="0 0 10 7"><path d="M1 1l4 4 4-4" fill="none" stroke="#333" stroke-width="1.6"/></svg></a>
  </nav>
</header>
<div class="abs dropdown">
  <a href="#">q7v.host</a>
  <a href="#">Brightwallfix</a>
  <a href="#">TKLS,Inc.</a>
  <a href="#">B&amp;J Construction</a>
</div>

<section class="abs hero" role="img" aria-label="Two IT engineers with a laptop in a server room with cloud network overlay"></section>
<h1 class="abs hero-title">Q7V CORP</h1>
<svg class="abs scroll-down" viewBox="0 0 54 54" aria-label="Scroll down"><circle cx="27" cy="27" r="25" fill="none" stroke="#fff" stroke-width="2.5"/><path d="M27 15v22M19 29l8 8 8-8" fill="none" stroke="#fff" stroke-width="2.5"/></svg>

<h2 class="abs section-title" style="top:680px">We Provide</h2>

<article class="abs provide-card" style="left:111px">
  <div class="photo" role="img" aria-label="Technician working at a server rack" style="background:linear-gradient(135deg,#3a3a3a,#7a6a62 50%,#2b2b2b)"></div>
  <h3>Services in IT</h3><p>Lorem ipsum dolor sit amet</p><a class="more" href="#">Read More »</a>
</article>
<article class="abs provide-card" style="left:359px">
  <div class="photo" role="img" aria-label="Laptop showing cloud computing on a desk" style="background:linear-gradient(135deg,#dfe6ea,#7fa3b8 50%,#4d5a63)"></div>
  <h3>Cloud/Hosting</h3><p>Lorem ipsum dolor sit amet</p><a class="more" href="#">Read More »</a>
</article>
<article class="abs provide-card" style="left:607px">
  <div class="photo" role="img" aria-label="Worker installing ceiling fixtures in a home" style="background:linear-gradient(135deg,#3b2a20,#a0683c 50%,#5a4030)"></div>
  <h3>Home/Commercial<br>Services</h3><p>Lorem ipsum dolor sit amet</p><a class="more" href="#">Read More »</a>
</article>
<article class="abs provide-card" style="left:855px">
  <div class="photo" role="img" aria-label="Construction workers inspecting a warehouse interior" style="background:linear-gradient(135deg,#cfd8de,#8ea3b1 50%,#6d7a82)"></div>
  <h3>Construction Services</h3><p>Lorem ipsum dolor sit amet</p><a class="more" href="#">Read More »</a>
</article>

<div class="abs wwd-back"></div>
<div class="abs wwd-photo" role="img" aria-label="Engineers in hard hats reviewing a tablet at an industrial site"></div>
<h2 class="abs wwd-title">What We Do</h2>
<p class="abs wwd-text">q7v Corp is a Corvane and Tallowbine IT Solution Provider. We provide support for Desktops, Laptops, Tablets, Mobile Devices,Networking, WiFi, Server, Design and more by providing Remote and OnSite Support Services. q7v Corp (Quick 7 Venture) Full service one stop shop service provider. Our CEO and Founder Lena Harrow has been working with Tallowbine Solutions all the way back to...</p>
<a class="abs btn wwd-btn" href="#">Read More</a>

<h2 class="abs section-title" style="top:1562px">Service Blog</h2>

<article class="abs blog-card" style="left:111px">
  <div class="photo" role="img" aria-label="Hands using a tablet and laptop at a desk" style="background:linear-gradient(135deg,#9aa3ad,#d9dde0 50%,#6f7a85)"><span class="tag">Q7V Corp</span></div>
  <h3>Lorem ipsum dolor sit amet, consectetur adipiscing</h3>
  <p>Sed ut perspiciatis unde omnis iste natus error sit voluptatem accusantium eaque ipsa quae ab illo inventore...<a href="#">Read More</a></p>
</article>
<article class="abs blog-card" style="left:442px">
  <div class="photo" role="img" aria-label="Smartphone showing a map app on a city street" style="background:linear-gradient(135deg,#b8a68c,#e6e1d8 50%,#8c7a64)"><span class="tag">Q7V Corp</span></div>
  <h3>Lorem ipsum dolor sit amet, consectetur adipiscing</h3>
  <p>Sed ut perspiciatis unde omnis iste natus error sit voluptatem accusantium eaque ipsa quae ab illo inventore...<a href="#">Read More</a></p>
</article>
<article class="abs blog-card" style="left:773px">
  <div class="photo" role="img" aria-label="Engineer working in a data center aisle" style="background:linear-gradient(135deg,#1c1c1c,#6a6a6a 50%,#2a2a2a)"><span class="tag">Q7V Corp</span></div>
  <h3>Lorem ipsum dolor sit amet, consectetur adipiscing</h3>
  <p>Sed ut perspiciatis unde omnis iste natus error sit voluptatem accusantium eaque ipsa quae ab illo inventore...<a href="#">Read More</a></p>
</article>

<section class="abs help-band" role="img" aria-label="Dark blue technology network background"></section>
<div class="abs tile" style="left:111px;top:2228px">
  <svg width="60" height="56" viewBox="0 0 60 56" fill="none" stroke="#fff" stroke-width="2"><circle cx="30" cy="20" r="9"/><circle cx="30" cy="20" r="15" stroke-dasharray="5 4"/><path d="M8 50c8-6 16-8 22-6s10 2 16-2 M8 50v-8"/></svg>IT Services</div>
<div class="abs tile" style="left:282px;top:2228px">
  <svg width="60" height="56" viewBox="0 0 60 56" fill="none" stroke="#fff" stroke-width="2"><path d="M12 32v-6a18 18 0 0 1 36 0v6"/><rect x="8" y="30" width="8" height="14" rx="3"/><rect x="44" y="30" width="8" height="14" rx="3"/><path d="M48 44c0 6-6 8-14 8"/><text x="30" y="36" font-size="14" fill="#fff" stroke="none" text-anchor="middle" font-family="Lato,sans-serif">24</text></svg>Support</div>
<div class="abs tile" style="left:111px;top:2378px">
  <svg width="60" height="56" viewBox="0 0 60 56" fill="none" stroke="#fff" stroke-width="2"><path d="M8 22l22-16 22 16v28H8z"/><path d="M8 22l22 16 22-16"/><path d="M16 16h28v12"/></svg>Email Services</div>
<div class="abs tile" style="left:282px;top:2378px">
  <svg width="60" height="56" viewBox="0 0 60 56" fill="none" stroke="#fff" stroke-width="2"><path d="M18 8l8 10-5 6c3 6 7 10 13 13l6-5 10 8-5 7c-16 0-32-16-32-32z"/></svg>+ 125 555 014</div>
<div class="abs help-box">
  <h2>How can we help?</h2>
  <p>Sed ut perspiciatis unde omnis iste natus error sit voluptatem accusantium doloremque laudantium,</p>
  <div class="field">Enter Your Email Address</div>
  <a class="send" href="#">SEND</a>
</div>

<div class="abs brand-name footer-brand">Q7V Corp</div>
<div class="abs socials" aria-label="Social profiles"><span></span><span></span><span></span><span></span><span></span></div>

<div class="abs foot-col" style="left:111px"><h4>Companies</h4><a>q7v.host</a><a>Brightwallfix</a><a>TKLS, Inc.,</a><a>B&amp;J Construction</a></div>
<div class="abs foot-col" style="left:297px"><h4>Navigation</h4><a>Home</a><a>About Us</a><a>Solutions</a><a>Support</a><a>Partners</a><a>Blog</a></div>
<div class="abs foot-col" style="left:472px"><h4>Other Links</h4><a>Faq</a><a>Privacy Policy</a><a>Terms &amp; Use</a><a>Sitemap</a><a>Contact Us</a></div>
<div class="abs foot-col" style="left:669px"><h4>Get In Touch</h4></div>
<div class="abs foot-input" style="left:669px;top:2867px;width:206px">First Name</div>
<div class="abs foot-input" style="left:882px;top:2867px;width:205px">Last name</div>
<div class="abs foot-input" style="left:669px;top:2911px;width:206px">Email Address</div>
<div class="abs foot-input" style="left:882px;top:2911px;width:205px">Phone No.</div>
<div class="abs foot-input" style="left:669px;top:2957px;width:418px;height:47px;line-height:26px">Message</div>
<a class="abs btn foot-send" href="#">Send</a>

<p class="abs copyright">copyright 2018 &nbsp;| Q7V Corp.All Rights Reserved.</p>

</body>
</html>
```